NCBG website design

We need a page template website design for a cms website. Please see the brief attached for the details.
The client is the National Copperfleece Breeders Guild which is an organisation promoting the Copperfleece Sheep Breed within Australia.
Updates

Project Deadline Extended
Reason: So that my top few designs can make changes and re-submit.

Target Market(s)

See attached brief

```html
<!DOCTYPE html>
<html lang="en">
<head>
<meta charset="utf-8">
<title>Copperfleece – National Copperfleece Breeders Guild</title>
<link href="https://fonts.googleapis.com/css2?family=Lato:ital,wght@0,400;0,700;1,400&family=Ubuntu:wght@500;700&family=Tinos&display=swap" rel="stylesheet">
<style>
:root{
  --green:#13a03a;
  --green-dark:#0d7f2c;
  --yellow:#f6c619;
  --dark:#2e2e2e;
  --ink:#333;
  --muted:#777;
  --line:#d6d6d6;
  --paper:#fff;
  --band:#f3f3f3;
}
*{box-sizing:border-box;margin:0;padding:0}
html,body{width:757px;height:1200px;overflow:hidden;background:var(--paper)}
body{position:relative;font-family:"Lato",sans-serif;color:var(--ink);font-size:8px}
.abs{position:absolute}
.hero-photo{left:0;top:0;width:757px;height:464px;
  background:linear-gradient(180deg,#5e6f86 0%,#8d8f8c 30%,#8c7d62 55%,#b89b6e 72%,#8e4f2a 92%,#7a3d20 100%)}
.hero-rule{left:0;top:462px;width:757px;height:3px;background:var(--yellow)}
.top-links{right:85px;top:12px;color:#eee;font-size:8px;display:flex;gap:14px}
.top-links span::before{content:"";display:inline-block;width:6px;height:7px;background:#ddd;margin-right:4px;border-radius:1px;vertical-align:-1px}
.logo{left:83px;top:16px;display:flex;align-items:center;gap:6px}
.logo-dot{width:44px;height:44px;border-radius:50%;background:var(--green);border:3px solid var(--yellow)}
.logo-name{font-size:17px;font-weight:700;color:#fff}
.contact-box{top:40px;height:32px;background:#fff;border-radius:2px;font-family:"Tinos",serif;padding:3px 8px;color:#444;font-size:8.5px;line-height:1.2}
.contact-box b{display:block;font-weight:400;color:var(--green);font-size:11px}
.nav{left:83px;top:86px;width:591px;height:29px;background:var(--dark);border-radius:4px;display:flex;align-items:center;overflow:hidden}
.nav a{color:#fff;text-decoration:none;font-size:8px;font-weight:700;padding:0 12.6px;line-height:29px;border-right:1px solid #444}
.nav a:last-child{border:0}
.nav a.active{background:var(--yellow);color:var(--dark)}
.hero-title{left:0;width:757px;top:164px;text-align:center;font-family:"Ubuntu",sans-serif;font-weight:700;color:#fff;font-size:17.5px;text-shadow:0 1px 3px rgba(0,0,0,.5)}
.hero-title em{font-style:normal;font-size:21px}
.hero-sub{left:130px;width:497px;top:193px;text-align:center;color:#f4f4f4;font-size:18px;font-weight:400;line-height:29px}
.btn{background:var(--yellow);color:var(--dark);font-weight:700;text-align:center;border-radius:1px}
.hero-btn{left:334px;top:257px;width:89px;height:24px;line-height:24px;font-size:11.5px}
.feature{top:436px;width:182px;height:48px;background:var(--green);border:2px solid var(--yellow);border-top:0;border-radius:3px;display:flex;align-items:center;gap:8px;padding-left:8px;color:#fff;box-shadow:0 2px 3px rgba(0,0,0,.2)}
.feature-icon{width:30px;height:30px;border-radius:50%;background:var(--green-dark);border:2px solid var(--yellow);display:grid;place-items:center;flex:none}
.feature h3{font-family:"Ubuntu",sans-serif;font-size:12px;font-weight:500}
.feature p{font-size:7.5px;margin-top:3px}
.sec-title{font-size:14px;font-weight:400;color:#222;display:flex;align-items:center;gap:6px;padding-bottom:6px;border-bottom:1px dashed var(--line)}
.sec-title span{color:var(--green)}
.welcome{left:83px;top:525px;width:390px}
.video{left:83px;top:558px;width:151px;height:82px;background:linear-gradient(180deg,#6d7b8c,#a38c6a 55%,#7a4c2d);}
.video-bar{left:83px;top:628px;width:151px;height:12px;background:#222}
.welcome-text{font-size:7.6px;line-height:12px;color:#444}
.wt1{left:248px;top:554px;width:225px}
.wt2{left:84px;top:647px;width:390px}
.read-more{left:83px;top:681px;width:58px;height:18px;line-height:18px;font-size:7.5px}
.divider{left:487px;top:525px;width:1px;height:170px;border-left:1px dashed #e2e2e2}
.quick{left:506px;top:525px;width:168px}
.field{left:506px;width:168px;height:16px;border:1px solid #ccc;font-size:7px;color:#777;padding:3px 5px;background:#fff}
.send{left:506px;top:681px;width:37px;height:18px;line-height:18px;font-size:7.5px}
.gallery{left:83px;top:718px;width:591px;height:155px;border:1px solid #ccc;border-radius:3px;background:#f6f6f6}
.gallery-tab{left:310px;top:718px;width:136px;height:24px;text-align:center;font-size:12.5px;line-height:22px;background:#f0f0f0;border:1px solid #ccc;border-top:0;border-radius:0 0 12px 12px}
.gallery-tab span{color:var(--green)}
.thumb{top:755px;width:101px;height:101px;background:#fff;border:1px solid #ccc;border-radius:2px;padding:5px}
.thumb.on{border:2px solid var(--yellow)}
.thumb-img{height:75px;background:linear-gradient(180deg,#6f8a54,#c9c3b2 50%,#7a9a50)}
.thumb-stats{font-size:7.5px;color:#555;margin-top:4px;display:flex;gap:8px}
.band{left:0;top:894px;width:757px;height:140px;background:var(--band)}
.avatar{left:98px;top:919px;width:64px;height:64px;border-radius:50%;background:linear-gradient(180deg,#7aa2c8,#d4a884);border:4px solid #fff;box-shadow:0 1px 4px rgba(0,0,0,.3)}
.quote{left:186px;top:922px;width:476px;font-size:7.6px;font-style:italic;line-height:14px;color:#444}
.quote b{font-weight:400;font-size:10.5px;color:#333}
.quote i{display:block;color:var(--green);font-size:10px;margin-top:2px}
.footer{left:0;top:990px;width:757px;height:210px}
.f-col{top:1062px;color:#ddd;font-size:7.5px}
.f-col h4{font-size:11.5px;font-weight:400;color:#eee;padding-bottom:7px;border-bottom:1px solid #444;margin-bottom:9px}
.f-row{display:flex;gap:8px;margin-bottom:6px;line-height:10px}
.f-row svg{flex:none;margin-top:1px}
.sponsor{width:140px;height:65px;background:#fff;display:flex;align-items:center;justify-content:center;font-size:14px;font-weight:700;color:#c8102e}
.sub-input{width:132px;height:16px;background:#fff;color:#777;padding:3px 4px;margin:8px 0 7px}
.sub-btn{width:59px;height:17px;line-height:17px;font-size:7.5px}
.f-logo{left:598px;top:1067px;width:56px;height:56px;border-radius:50%;background:var(--green);border:3px solid var(--yellow)}
.f-social{left:582px;top:1136px;width:87px;height:24px;border:2px solid #9ab;background:#fff;border-radius:2px;color:#3b5998;font-size:8px;font-weight:700;text-align:center;line-height:20px}
.copy{left:0;top:1183px;width:757px;text-align:center;color:#eee;font-size:7.5px}
</style>
</head>
<body>
<div class="abs hero-photo" role="img" aria-label="Flock of sheep standing on red earth in front of wooded hills"></div>
<div class="abs hero-rule"></div>

<div class="abs logo"><div class="logo-dot"></div><div class="logo-name">Copperfleece</div></div>
<div class="abs top-links"><span>Members Resources</span><span>Web Manager Login</span></div>
<div class="abs contact-box" style="left:412px;width:104px">Call Now:<b>(08) 7300 4418</b></div>
<div class="abs contact-box" style="left:522px;width:152px">Email us:<b>hello@copperfleece.org</b></div>

<nav class="abs nav">
  <a class="active">HOME</a><a>ABOUT</a><a>SEARCH</a><a>MEMBER SERVICES</a><a>STUD PAGES</a><a>NEWS</a><a>SALES</a><a>LINK</a><a>CONTACT</a>
</nav>

<h1 class="abs hero-title">The Copperfleece Is An Australian <em>Sheep Breed Development</em></h1>
<p class="abs hero-sub">We helps to market, promote and educate people about the advantages of the breed.</p>
<div class="abs btn hero-btn">READ MORE</div>

<div class="abs feature" style="left:90px"><div class="feature-icon"><svg width="14" height="14" viewBox="0 0 14 14"><circle cx="7" cy="5" r="3" fill="#fff"/><path d="M2 13c0-3 2-5 5-5s5 2 5 5z" fill="#fff"/></svg></div><div><h3>Prime Lamb Helpline</h3><p>Lorem ipsum dolor sit</p></div></div>
<div class="abs feature" style="left:287px"><div class="feature-icon"><svg width="14" height="14" viewBox="0 0 14 14"><rect x="1" y="2" width="12" height="11" fill="none" stroke="#fff" stroke-width="1.5"/><path d="M1 5h12" stroke="#fff"/></svg></div><div><h3>Upcoming Events</h3><p>major show and sales</p></div></div>
<div class="abs feature" style="left:485px"><div class="feature-icon"><svg width="14" height="14" viewBox="0 0 14 14"><rect x="2" y="2" width="10" height="10" fill="none" stroke="#fff" stroke-width="1.5"/><path d="M4 5h6M4 7h6M4 9h6" stroke="#fff"/></svg></div><div><h3>Latest News</h3><p>And media releases</p></div></div>

<div class="abs welcome"><h2 class="sec-title"><svg width="18" height="18"><circle cx="9" cy="9" r="8" fill="var(--green)"/></svg>Welcome to <span>Copperfleece</span></h2></div>
<div class="abs video" role="img" aria-label="Video still of sheep in a paddock"></div>
<div class="abs video-bar"></div>
<svg class="abs" style="left:146px;top:583px" width="26" height="18"><rect width="26" height="18" rx="4" fill="#d61f1f"/><path d="M10 5l7 4-7 4z" fill="#fff"/></svg>
<div class="abs welcome-text wt1"><p>Lorem ipsum dolor sit amet, consectetuer adipscing sed diayi nibh euismod tincidunt ut laoreet dolore magna aliquam erati volutpat. Ut wisi eiam, quis nostrud exerci tation ullamcorper suscipit lobortis nisl ut aliquip ex ea commodo consequat.</p><p style="margin-top:12px">Duis autem vel eum iriure dolor in hendrerit in vulputte veliti esse molestie consequat illum dolore eu feugiat nulla facilisisi</p></div>
<p class="abs welcome-text wt2">Lorem ipsum dolor sit amet, consectetuer adipscing sed diayi nibh euismod tincidunt ut laoreetlore magna aliquam erati volutpat. Ut wisi eiam, quis nostrud exerci.</p>
<div class="abs btn read-more">READ MORE</div>

<div class="abs divider"></div>
<div class="abs quick"><h2 class="sec-title"><svg width="24" height="18" viewBox="0 0 24 18"><path d="M3 14l6-9 4 3 4-6M3 3l3 3" stroke="#444" stroke-width="1.6" fill="none"/></svg>Quick <span>Contact</span></h2></div>
<div class="abs field" style="top:557px">Name</div>
<div class="abs field" style="top:578px">Email</div>
<div class="abs field" style="top:600px">Phone</div>
<div class="abs field" style="top:621px;height:46px">Comment</div>
<div class="abs btn send">SEND</div>

<div class="abs gallery"></div>
<div class="abs gallery-tab">Our <span>Gallery</span></div>
<div class="abs thumb on" style="left:95px"><div class="thumb-img" role="img" aria-label="Sheep standing on grass"></div><div class="thumb-stats"><span>◉ 123</span><span>♥ 4</span></div></div>
<div class="abs thumb" style="left:212px"><div class="thumb-img" role="img" aria-label="Woolly sheep grazing" style="background:linear-gradient(180deg,#8e8a5c,#b59c6c)"></div><div class="thumb-stats"><span>◉ 423</span><span>♥ 10</span></div></div>
<div class="abs thumb" style="left:329px"><div class="thumb-img" role="img" aria-label="Flock of sheep in a field" style="background:linear-gradient(180deg,#9ab07a,#b9a98a)"></div><div class="thumb-stats"><span>◉ 100</span><span>♥ 24</span></div></div>
<div class="abs thumb" style="left:446px"><div class="thumb-img" role="img" aria-label="Sheep beneath a tree" style="background:linear-gradient(180deg,#5c6e45,#c5c0ad)"></div><div class="thumb-stats"><span>◉ 104</span><span>♥ 11</span></div></div>
<div class="abs thumb" style="left:562px"><div class="thumb-img" role="img" aria-label="White lambs close up" style="background:linear-gradient(180deg,#6d8c4a,#e3ddd0)"></div><div class="thumb-stats"><span>◉ 189</span><span>♥ 2</span></div></div>

<div class="abs band"></div>
<div class="abs avatar" role="img" aria-label="Portrait of member"></div>
<div class="abs quote"><b>“ Copperfleece is</b> ipsum dolor sit amet, consectetuer adipscing sed diayi nibh euismod tincidunt ut laoreet dolore magna aliquam erati volutpat. Ut wisi eiam, quis nostrud exerci tation ullamcorper suscipit lobortis nisl ut aliquip ex ea codo conseauis autem vel eum iriure dolor in hendrerit in vulputte veliti esse molestie consequat illum dolore eu feugiat nulla facilisisi<i>Mr. Dolore Eu Feugiat</i></div>

<svg class="abs footer" viewBox="0 0 757 210" preserveAspectRatio="none">
  <path d="M0 30 C200 5 500 55 757 0 V210 H0Z" fill="var(--dark)"/>
  <path d="M25 20 C250 5 520 60 757 0 V8 C520 70 250 15 25 20Z" fill="var(--green)"/>
</svg>

<div class="abs f-col" style="left:84px;width:128px"><h4>Contact Information</h4>
  <div class="f-row"><svg width="8" height="9"><path d="M4 9L1 4a3 3 0 116 0z" fill="#ddd"/></svg><span>PO Box 42,<br>Millbrook, SA 5099</span></div>
  <div class="f-row"><svg width="8" height="9"><path d="M1 1h2l1 2-1 1a5 5 0 003 3l1-1 2 1v2C4 9 0 5 1 1z" fill="#ddd"/></svg><span>(08) 7300 4418</span></div>
  <div class="f-row"><svg width="8" height="9"><rect x="0" y="3" width="8" height="4" fill="#ddd"/><rect x="2" y="0" width="4" height="3" fill="#ddd"/></svg><span>(08) 7300 4419</span></div>
  <div class="f-row"><svg width="8" height="9"><path d="M0 2h8v6H0z M0 2l4 3 4-3" fill="none" stroke="#ddd"/></svg><span>hello@copperfleece.org</span></div>
</div>
<div class="abs f-col" style="left:239px;width:140px"><h4>Our Sponsors</h4><div class="sponsor">Northway Vision</div></div>
<div class="abs f-col" style="left:408px;width:153px"><h4>Newsletter Sign Up</h4><p style="line-height:12px">Lorem ipsudolor sit coec adipiscing elitsite amet</p><div class="sub-input">Email Address</div><div class="btn sub-btn">SUBSCRIBE</div></div>
<div class="abs f-logo"></div>
<div class="abs f-social">Find us on Flockbook</div>
<p class="abs copy">Copyright © 2014, Copperfleece. All Rights Reserved</p>
</body>
</html>
```